Design a Travel and Tourism website

We would like a freelancer to design a website that is essentially easy to use and navigate database providing local information for Travelers about destination countries.

We proposed website would discuss different rates, fees, visa requirement, resort locations, cheap flights, etc. This website should be elegant and modern. Our business name is rovanix.
Some reference websites are zemplorift.ca, brindlefoxhaven.com,
There should be a forum in the website where travell\ers discuss about their first hand tranvel experience to such destinations.

Tourism

```html
<!DOCTYPE html>
<html lang="en">
<head>
<meta charset="utf-8">
<title>Rovanix — Start Your Dream Holidays</title>
<link rel="stylesheet" href="https://fonts.googleapis.com/css2?family=Montserrat:wght@500;600;700&family=Merienda:wght@400;700&family=Roboto:wght@400;500;700&display=swap">
<style>
:root{
  --gold:#b39456;
  --gold-light:#e8dcc2;
  --blue:#1a86cf;
  --blue-dark:#0f6fb4;
  --navy:#17233f;
  --panel:rgba(14,22,42,.86);
  --tab-dark:#3e4249;
  --ink:#2b2b2b;
  --muted:#666;
  --grey-bg:#f0f0f0;
  --white:#fff;
}
*{margin:0;padding:0;box-sizing:border-box}
html,body{width:1200px;height:2564px;overflow:hidden}
body{position:relative;background:var(--white);font-family:'Roboto',sans-serif;color:var(--ink)}
.abs{position:absolute}

/* header */
.top-strip{left:0;top:0;width:1200px;height:24px;background:var(--navy)}
.top-strip a{position:absolute;top:6px;font:600 9px 'Montserrat',sans-serif;color:#d6c49a;text-decoration:none;letter-spacing:.5px}
.main-nav{left:0;top:24px;width:1200px;height:41px;background:var(--blue)}
.main-nav a{position:absolute;top:0;height:41px;line-height:41px;font:700 12px 'Montserrat',sans-serif;color:var(--white);text-decoration:none;transform:translateX(-50%);letter-spacing:.4px}
.main-nav a.active{background:var(--gold);width:77px;text-align:center}
.logo-tab{left:516px;top:0;width:168px;height:104px}
.logo-tab .brand{position:absolute;left:0;top:34px;width:168px;text-align:center;font:700 26px 'Montserrat',sans-serif;color:var(--navy);letter-spacing:1px}

/* hero */
.hero-photo{left:0;top:65px;width:1200px;height:554px;background:linear-gradient(160deg,#2b9cae 0%,#1d7f8c 28%,#3f6b3a 50%,#24595d 70%,#0f3346 100%)}
.hero-title{left:142px;top:262px;font:700 47px/1.08 'Montserrat',sans-serif;color:var(--white);text-transform:uppercase}
.slide-dots{left:1181px;top:215px;width:6px}
.slide-dots span{display:block;width:6px;height:6px;border-radius:50%;background:rgba(255,255,255,.75);margin-bottom:8px}
.promo-badge{left:871px;top:167px;width:178px;height:178px;border-radius:50%;border:3px solid var(--gold);background:rgba(17,44,60,.72);text-align:center;color:var(--white)}
.promo-badge .city{margin-top:46px;font:700 24px 'Merienda',cursive}
.promo-badge .price{font:500 12px 'Roboto',sans-serif}
.promo-badge .price b{font:700 19px 'Roboto',sans-serif;color:var(--gold-light)}
.promo-badge .badge-brand{margin-top:8px;font:700 13px 'Montserrat',sans-serif;color:var(--blue)}
.promo-badge .star-cap{position:absolute;left:69px;top:-3px}

/* search */
.search-panel{left:0;top:410px;width:1200px;height:209px;background:var(--panel)}
.search-tabs{left:301px;top:444px;display:flex;gap:10px}
.search-tabs span{height:28px;line-height:28px;padding:0 14px;background:var(--tab-dark);color:var(--white);font:700 13px 'Merienda',cursive}
.search-tabs span.active{background:var(--gold)}
.field-label{top:483px;font:700 8px 'Montserrat',sans-serif;color:var(--white);letter-spacing:.3px}
.field{top:497px;height:37px;background:var(--white);border:1px solid #ccc;font:400 11px 'Roboto',sans-serif;color:#999;display:flex;align-items:center;padding-left:12px;gap:7px}
.field.select{color:var(--ink);font-size:15px;justify-content:space-between;padding-right:10px}
.add-car{left:455px;top:559px;font:700 13px 'Merienda',cursive;color:var(--white);display:flex;align-items:center;gap:6px}
.add-car i{display:inline-block;width:10px;height:10px;background:var(--white);border:1px solid #bbb}
.btn-blue{background:var(--blue);color:var(--white);text-align:center;font:700 15px 'Merienda',cursive}
.search-btn{left:552px;top:550px;width:96px;height:38px;line-height:38px}

/* favourites */
.section-title{left:0;width:1200px;text-align:center;font:700 26px 'Montserrat',sans-serif;color:#333;text-transform:uppercase}
.fav-tabs-line{left:390px;top:738px;width:668px;height:1px;background:#ddd}
.fav-tab{top:709px;height:29px;line-height:29px;font:400 13px 'Merienda',cursive;color:var(--gold);transform:translateX(-50%)}
.fav-tab.active{background:var(--gold);color:var(--white);width:104px;text-align:center}
.deal-card{top:778px;width:221px;height:194px;overflow:hidden}
.deal-card .label{position:absolute;left:8px;bottom:10px;font:400 13px 'Merienda',cursive;color:var(--white)}
.deal-card .corner{position:absolute;right:0;bottom:0}
.deal-card .overlay{position:absolute;left:0;top:64px;width:100%;text-align:center;color:var(--white)}
.deal-card .overlay .name{font:400 27px 'Merienda',cursive}
.deal-card .overlay .from{font:400 13px 'Merienda',cursive}
.deal-card .overlay b{font-size:16px}
.carousel-dots{left:576px;top:993px;display:flex;gap:7px}
.carousel-dots span{width:5px;height:5px;border-radius:50%;background:#ccc}
.carousel-dots span.on{background:var(--gold)}

/* forum */
.forum-bg{left:0;top:1051px;width:1200px;height:610px;background:var(--grey-bg)}
.subtitle{left:0;width:1200px;text-align:center;font:400 13px 'Merienda',cursive;color:var(--gold)}
.forum-table{left:142px;top:1183px;width:916px;border:1px solid #e1d7c1;background:var(--white)}
.forum-head{height:36px;background:var(--gold);position:relative;font:700 10px 'Montserrat',sans-serif;color:var(--white)}
.forum-head span{position:absolute;top:13px}
.forum-row{height:66px;position:relative;border-top:1px solid #e8e8e8}
.forum-row:first-of-type{border-top:none}
.forum-row .topic{position:absolute;left:24px;top:19px;font:600 14px 'Montserrat',sans-serif;color:var(--gold)}
.forum-row .author{position:absolute;left:24px;top:39px;font:400 10px 'Roboto',sans-serif;color:#444}
.forum-row .date{position:absolute;left:547px;top:20px;font:400 10px 'Roboto',sans-serif;color:#555}
.forum-row .stats{position:absolute;right:22px;top:20px;font:400 10px/1.35 'Roboto',sans-serif;color:#555;text-align:right}
.forum-row .stats em{font-style:normal;color:var(--gold)}
.view-all{left:552px;top:1577px;width:96px;height:31px;line-height:31px;font-size:14px}

/* newsletter */
.newsletter{left:0;top:1661px;width:1200px;height:174px;background:linear-gradient(90deg,#0f6fb4 0%,#1a86cf 55%,#2a8fd0 100%)}
.newsletter-title{left:0;top:1703px;width:1200px;text-align:center;font:700 18px 'Montserrat',sans-serif;color:var(--white)}
.newsletter-sub{left:0;top:1726px;width:1200px;text-align:center;font:400 13px 'Merienda',cursive;color:var(--white)}
.email-input{left:381px;top:1753px;width:341px;height:38px;background:var(--white);display:flex;align-items:center;gap:8px;padding-left:15px;font:400 11px 'Roboto',sans-serif;color:#999}
.submit-btn{left:728px;top:1753px;width:91px;height:38px;line-height:38px;background:var(--gold);color:var(--white);text-align:center;font:700 15px 'Merienda',cursive}

/* popular links */
.pop-link{width:289px;height:51px}
.pop-link svg.frame{position:absolute;left:0;top:0}
.pop-link .text{position:absolute;left:18px;top:0;height:51px;display:flex;align-items:center;gap:14px;font:400 15px 'Merienda',cursive;color:#333}

/* footer */
.footer-brand{left:0;top:2312px;width:1200px;text-align:center;font:700 28px 'Montserrat',sans-serif;color:var(--navy);letter-spacing:1px}
.footer-links{left:0;top:2380px;width:1200px;display:flex;justify-content:center;gap:26px;font:700 10px 'Montserrat',sans-serif;color:#222}
.copyright{left:0;top:2402px;width:1200px;text-align:center;font:500 10px 'Roboto',sans-serif;color:#444;letter-spacing:.6px}
.skyline{left:0;top:2430px;width:1200px;height:134px;background:linear-gradient(180deg,rgba(179,148,86,0) 0%,rgba(179,148,86,.55) 35%,var(--gold) 70%,#9a7b3f 100%)}
</style>
</head>
<body>

<!-- header -->
<div class="abs top-strip">
  <a style="left:880px">ACCOUNT ▾</a>
  <a style="left:948px">MY TRIPS</a>
  <a style="left:1010px">SUPPORT ▾</a>
</div>

<div class="abs hero-photo" role="img" aria-label="Aerial view of a turquoise bay with islands, boats and a coastal town"></div>

<nav class="abs main-nav">
  <a class="active" style="left:180px">HOME</a>
  <a style="left:268px">HOLIDAYS</a>
  <a style="left:362px">FLIGHTS</a>
  <a style="left:453px">HOTELS</a>
  <a style="left:743px">CARS</a>
  <a style="left:820px">DEALS</a>
  <a style="left:916px">INSURANCE</a>
  <a style="left:1013px">FORUM</a>
</nav>

<div class="abs logo-tab">
  <svg width="168" height="104" viewBox="0 0 168 104"><path d="M0 0H168V70Q168 80 158 84L94 101Q84 104 74 101L10 84Q0 80 0 70Z" fill="#fff"/></svg>
  <div class="brand">ROVANIX</div>
</div>

<h1 class="abs hero-title">Start your dream<br>holidays right here</h1>

<div class="abs slide-dots"><span></span><span></span><span></span><span></span></div>

<div class="abs promo-badge">
  <svg class="star-cap" width="34" height="30" viewBox="0 0 34 30"><path d="M0 0H34V22Q17 34 0 22Z" fill="#b39456"/><path d="M17 4l2.6 5.4 5.9.8-4.3 4.1 1 5.8L17 17.3 11.8 20l1-5.8-4.3-4.1 5.9-.8z" fill="#17233f"/></svg>
  <div class="city">Berlin</div>
  <div class="price">From <b>$500</b> per person</div>
  <div class="badge-brand">ROVANIX</div>
</div>

<!-- search -->
<div class="abs search-panel"></div>
<div class="abs search-tabs">
  <span class="active">Flight &amp; Hotel</span><span>Holidays</span><span>Flights</span><span>Hotels</span><span>Cars</span><span>Insurance</span><span>Extras</span>
</div>

<span class="abs field-label" style="left:142px">FLYING FROM</span>
<span class="abs field-label" style="left:373px">FLYING TO</span>
<span class="abs field-label" style="left:603px">DEPARTING</span>
<span class="abs field-label" style="left:728px">RETURNING</span>
<span class="abs field-label" style="left:853px">ROOMS</span>
<span class="abs field-label" style="left:909px">ADULTS (18+)</span>
<span class="abs field-label" style="left:981px">CHILDREN (0-17)</span>

<div class="abs field" style="left:142px;width:225px"><svg width="9" height="12" viewBox="0 0 9 12"><path d="M4.5 0A4.5 4.5 0 0 0 0 4.5C0 8 4.5 12 4.5 12S9 8 9 4.5A4.5 4.5 0 0 0 4.5 0Zm0 6.3a1.8 1.8 0 1 1 0-3.6 1.8 1.8 0 0 1 0 3.6Z" fill="#aaa"/></svg>City or Airport</div>
<div class="abs field" style="left:373px;width:225px"><svg width="9" height="12" viewBox="0 0 9 12"><path d="M4.5 0A4.5 4.5 0 0 0 0 4.5C0 8 4.5 12 4.5 12S9 8 9 4.5A4.5 4.5 0 0 0 4.5 0Zm0 6.3a1.8 1.8 0 1 1 0-3.6 1.8 1.8 0 0 1 0 3.6Z" fill="#aaa"/></svg>City or Airport</div>
<div class="abs field" style="left:603px;width:120px"><svg width="12" height="12" viewBox="0 0 12 12"><rect x=".5" y="1.5" width="11" height="10" fill="none" stroke="#aaa"/><path d="M.5 4.5h11M3 0v3M9 0v3" stroke="#aaa"/></svg>dd/mm/yyyy</div>
<div class="abs field" style="left:728px;width:120px"><svg width="12" height="12" viewBox="0 0 12 12"><rect x=".5" y="1.5" width="11" height="10" fill="none" stroke="#aaa"/><path d="M.5 4.5h11M3 0v3M9 0v3" stroke="#aaa"/></svg>dd/mm/yyyy</div>
<div class="abs field select" style="left:853px;width:51px">1<svg width="10" height="6" viewBox="0 0 10 6"><path d="M1 1l4 4 4-4" fill="none" stroke="#333" stroke-width="1.5"/></svg></div>
<div class="abs field select" style="left:909px;width:67px">2<svg width="10" height="6" viewBox="0 0 10 6"><path d="M1 1l4 4 4-4" fill="none" stroke="#333" stroke-width="1.5"/></svg></div>
<div class="abs field select" style="left:981px;width:77px">0<svg width="10" height="6" viewBox="0 0 10 6"><path d="M1 1l4 4 4-4" fill="none" stroke="#333" stroke-width="1.5"/></svg></div>

<div class="abs add-car"><i></i>Add a Car</div>
<div class="abs btn-blue search-btn">Search</div>

<!-- favourites -->
<h2 class="abs section-title" style="top:668px">Select your favourites</h2>
<div class="abs fav-tabs-line"></div>
<div class="abs fav-tab active" style="left:442px">Top Deals</div>
<div class="abs fav-tab" style="left:585px">Featured Destinations</div>
<div class="abs fav-tab" style="left:754px">Popular Packages</div>

<div class="abs deal-card" style="left:142px">
  <div class="abs" style="inset:0;background:linear-gradient(160deg,#c9d3dd 0%,#7a8796 45%,#3b4450 100%)" role="img" aria-label="City skyscrapers seen from street level"></div>
  <span class="label">Newyork Deals</span>
  <svg class="corner" width="34" height="34" viewBox="0 0 34 34"><path d="M34 0V34H0Z" fill="#b39456"/><path d="M24 16l1.9 3.9 4.3.6-3.1 3 .7 4.3L24 25.8l-3.8 2 .7-4.3-3.1-3 4.3-.6z" fill="#17233f"/></svg>
</div>
<div class="abs deal-card" style="left:373px">
  <div class="abs" style="inset:0;background:linear-gradient(170deg,#e88c3c 0%,#a9476a 45%,#3c3b6e 100%)" role="img" aria-label="Las Vegas welcome sign at dusk"></div>
  <span class="label">Las Vegas Deals</span>
  <svg class="corner" width="34" height="34" viewBox="0 0 34 34"><path d="M34 0V34H0Z" fill="#b39456"/><path d="M24 16l1.9 3.9 4.3.6-3.1 3 .7 4.3L24 25.8l-3.8 2 .7-4.3-3.1-3 4.3-.6z" fill="#17233f"/></svg>
</div>
<div class="abs deal-card" style="left:605px">
  <div class="abs" style="inset:0;background:linear-gradient(180deg,#5fa4d8 0%,#2f7fbf 55%,#1e5e95 100%)" role="img" aria-label="Bangkok temple under a blue sky"></div>
  <div class="overlay"><div class="name">Bangkok Deals</div><div class="from">From <b>$500</b> per person</div></div>
  <svg class="corner" width="34" height="34" viewBox="0 0 34 34"><path d="M34 0V34H0Z" fill="#b39456"/><path d="M24 16l1.9 3.9 4.3.6-3.1 3 .7 4.3L24 25.8l-3.8 2 .7-4.3-3.1-3 4.3-.6z" fill="#17233f"/></svg>
</div>
<div class="abs deal-card" style="left:836px">
  <div class="abs" style="inset:0;background:linear-gradient(180deg,#a9c7d6 0%,#5f8e74 45%,#b58e74 100%)" role="img" aria-label="Hula dancer on a Hawaiian beach"></div>
  <span class="label">Hawaii Deals</span>
  <svg class="corner" width="34" height="34" viewBox="0 0 34 34"><path d="M34 0V34H0Z" fill="#b39456"/><path d="M24 16l1.9 3.9 4.3.6-3.1 3 .7 4.3L24 25.8l-3.8 2 .7-4.3-3.1-3 4.3-.6z" fill="#17233f"/></svg>
</div>
<div class="abs carousel-dots"><span class="on"></span><span></span><span></span><span></span></div>

<!-- forum -->
<div class="abs forum-bg"></div>
<h2 class="abs section-title" style="top:1103px">Latest travel forum</h2>
<p class="abs subtitle" style="top:1133px">Please share your experience here</p>

<div class="abs forum-table">
  <div class="forum-head"><span style="left:24px">TITLE</span><span style="left:547px">POSTED ON</span><span style="right:22px">VIEWS / REPLIES</span></div>
  <div class="forum-row"><span class="topic">Why Hawaii is a hub for entertainment?</span><span class="author">By : Ansel Varrick</span><span class="date">15 Jan 2017, 07:45 AM</span><span class="stats">View : 1450<br>Replies : <em>45</em></span></div>
  <div class="forum-row"><span class="topic">Whis the hottest place in January?</span><span class="author">By : Dorin Kessly</span><span class="date">15 Jan 2017, 06:45 AM</span><span class="stats">View : 1950<br>Replies : <em>75</em></span></div>
  <div class="forum-row"><span class="topic">Must visit destinations in the world which make you feel better...</span><span class="author">By : Dorin Kessly</span><span class="date">15 Jan 2017, 06:45 AM</span><span class="stats">View : 1950<br>Replies : <em>75</em></span></div>
  <div class="forum-row"><span class="topic">Why Hawaii is a hub for entertainment?</span><span class="author">By : Ansel Varrick</span><span class="date">15 Jan 2017, 07:45 AM</span><span class="stats">View : 1450<br>Replies : <em>45</em></span></div>
  <div class="forum-row"><span class="topic">Whis the hottest place in January?</span><span class="author">By : Dorin Kessly</span><span class="date">15 Jan 2017, 06:45 AM</span><span class="stats">View : 1950<br>Replies : <em>75</em></span></div>
</div>
<div class="abs btn-blue view-all">View All</div>

<!-- newsletter -->
<div class="abs newsletter" role="img" aria-label="Blue-tinted lake scene with a moored boat"></div>
<h3 class="abs newsletter-title">SIGN UP TO OUR NEWSLETTER</h3>
<p class="abs newsletter-sub">Get updated for special offers</p>
<div class="abs email-input"><svg width="12" height="9" viewBox="0 0 12 9"><rect width="12" height="9" fill="#b39456"/><path d="M0 0l6 5 6-5" fill="none" stroke="#fff"/></svg>Enter your email address</div>
<div class="abs submit-btn">Submit</div>

<!-- popular links -->
<h2 class="abs section-title" style="top:1888px">Popular links you may interested</h2>

<div class="abs" style="left:0;top:0">
</div>
<!-- row 1 -->
<div class="abs pop-link" style="left:142px;top:1953px"><svg class="frame" width="289" height="51" viewBox="0 0 289 51"><path d="M6 .5H268L288 25.5 268 50.5H6Q.5 50.5 .5 45V6Q.5 .5 6 .5Z" fill="#fff" stroke="#e6dcc6"/></svg><span class="text"><svg width="14" height="11" viewBox="0 0 14 11"><path d="M1 6l4 4 8-9" fill="none" stroke="#b39456" stroke-width="2"/></svg>New York Holidays</span></div>
<div class="abs pop-link" style="left:455px;top:1953px"><svg class="frame" width="289" height="51" viewBox="0 0 289 51"><path d="M6 .5H268L288 25.5 268 50.5H6Q.5 50.5 .5 45V6Q.5 .5 6 .5Z" fill="#fff" stroke="#e6dcc6"/></svg><span class="text"><svg width="14" height="11" viewBox="0 0 14 11"><path d="M1 6l4 4 8-9" fill="none" stroke="#b39456" stroke-width="2"/></svg>Amsterdam Hotels</span></div>
<div class="abs pop-link" style="left:767px;top:1953px"><svg class="frame" width="289" height="51" viewBox="0 0 289 51"><path d="M6 .5H268L288 25.5 268 50.5H6Q.5 50.5 .5 45V6Q.5 .5 6 .5Z" fill="#fff" stroke="#e6dcc6"/></svg><span class="text"><svg width="14" height="11" viewBox="0 0 14 11"><path d="M1 6l4 4 8-9" fill="none" stroke="#b39456" stroke-width="2"/></svg>Dubai Holidays</span></div>
<!-- row 2 -->
<div class="abs pop-link" style="left:142px;top:2013px"><svg class="frame" width="289" height="51" viewBox="0 0 289 51"><path d="M6 .5H268L288 25.5 268 50.5H6Q.5 50.5 .5 45V6Q.5 .5 6 .5Z" fill="#fff" stroke="#e6dcc6"/></svg><span class="text"><svg width="14" height="11" viewBox="0 0 14 11"><path d="M1 6l4 4 8-9" fill="none" stroke="#b39456" stroke-width="2"/></svg>UK Car Hire</span></div>
<div class="abs pop-link" style="left:455px;top:2013px"><svg class="frame" width="289" height="51" viewBox="0 0 289 51"><path d="M6 .5H268L288 25.5 268 50.5H6Q.5 50.5 .5 45V6Q.5 .5 6 .5Z" fill="#fff" stroke="#e6dcc6"/></svg><span class="text"><svg width="14" height="11" viewBox="0 0 14 11"><path d="M1 6l4 4 8-9" fill="none" stroke="#b39456" stroke-width="2"/></svg>Oralando Flights</span></div>
<div class="abs pop-link" style="left:767px;top:2013px"><svg class="frame" width="289" height="51" viewBox="0 0 289 51"><path d="M6 .5H268L288 25.5 268 50.5H6Q.5 50.5 .5 45V6Q.5 .5 6 .5Z" fill="#fff" stroke="#e6dcc6"/></svg><span class="text"><svg width="14" height="11" viewBox="0 0 14 11"><path d="M1 6l4 4 8-9" fill="none" stroke="#b39456" stroke-width="2"/></svg>Bangkok Flights</span></div>
<!-- row 3 -->
<div class="abs pop-link" style="left:142px;top:2073px"><svg class="frame" width="289" height="51" viewBox="0 0 289 51"><path d="M6 .5H268L288 25.5 268 50.5H6Q.5 50.5 .5 45V6Q.5 .5 6 .5Z" fill="#fff" stroke="#e6dcc6"/></svg><span class="text"><svg width="14" height="11" viewBox="0 0 14 11"><path d="M1 6l4 4 8-9" fill="none" stroke="#b39456" stroke-width="2"/></svg>Sydney Flights</span></div>
<div class="abs pop-link" style="left:455px;top:2073px"><svg class="frame" width="289" height="51" viewBox="0 0 289 51"><path d="M6 .5H268L288 25.5 268 50.5H6Q.5 50.5 .5 45V6Q.5 .5 6 .5Z" fill="#fff" stroke="#e6dcc6"/></svg><span class="text"><svg width="14" height="11" viewBox="0 0 14 11"><path d="M1 6l4 4 8-9" fill="none" stroke="#b39456" stroke-width="2"/></svg>Hawaii Hotels</span></div>
<div class="abs pop-link" style="left:767px;top:2073px"><svg class="frame" width="289" height="51" viewBox="0 0 289 51"><path d="M6 .5H268L288 25.5 268 50.5H6Q.5 50.5 .5 45V6Q.5 .5 6 .5Z" fill="#fff" stroke="#e6dcc6"/></svg><span class="text"><svg width="14" height="11" viewBox="0 0 14 11"><path d="M1 6l4 4 8-9" fill="none" stroke="#b39456" stroke-width="2"/></svg>Paris Car Hire</span></div>
<!-- row 4 -->
<div class="abs pop-link" style="left:142px;top:2133px"><svg class="frame" width="289" height="51" viewBox="0 0 289 51"><path d="M6 .5H268L288 25.5 268 50.5H6Q.5 50.5 .5 45V6Q.5 .5 6 .5Z" fill="#fff" stroke="#e6dcc6"/></svg><span class="text"><svg width="14" height="11" viewBox="0 0 14 11"><path d="M1 6l4 4 8-9" fill="none" stroke="#b39456" stroke-width="2"/></svg>New York Holidays</span></div>
<div class="abs pop-link" style="left:455px;top:2133px"><svg class="frame" width="289" height="51" viewBox="0 0 289 51"><path d="M6 .5H268L288 25.5 268 50.5H6Q.5 50.5 .5 45V6Q.5 .5 6 .5Z" fill="#fff" stroke="#e6dcc6"/></svg><span class="text"><svg width="14" height="11" viewBox="0 0 14 11"><path d="M1 6l4 4 8-9" fill="none" stroke="#b39456" stroke-width="2"/></svg>Amsterdam Hotels</span></div>
<div class="abs pop-link" style="left:767px;top:2133px"><svg class="frame" width="289" height="51" viewBox="0 0 289 51"><path d="M6 .5H268L288 25.5 268 50.5H6Q.5 50.5 .5 45V6Q.5 .5 6 .5Z" fill="#fff" stroke="#e6dcc6"/></svg><span class="text"><svg width="14" height="11" viewBox="0 0 14 11"><path d="M1 6l4 4 8-9" fill="none" stroke="#b39456" stroke-width="2"/></svg>Dubai Holidays</span></div>
<!-- row 5 -->
<div class="abs pop-link" style="left:142px;top:2193px"><svg class="frame" width="289" height="51" viewBox="0 0 289 51"><path d="M6 .5H268L288 25.5 268 50.5H6Q.5 50.5 .5 45V6Q.5 .5 6 .5Z" fill="#fff" stroke="#e6dcc6"/></svg><span class="text"><svg width="14" height="11" viewBox="0 0 14 11"><path d="M1 6l4 4 8-9" fill="none" stroke="#b39456" stroke-width="2"/></svg>UK Car Hire</span></div>
<div class="abs pop-link" style="left:455px;top:2193px"><svg class="frame" width="289" height="51" viewBox="0 0 289 51"><path d="M6 .5H268L288 25.5 268 50.5H6Q.5 50.5 .5 45V6Q.5 .5 6 .5Z" fill="#fff" stroke="#e6dcc6"/></svg><span class="text"><svg width="14" height="11" viewBox="0 0 14 11"><path d="M1 6l4 4 8-9" fill="none" stroke="#b39456" stroke-width="2"/></svg>Oralando Flights</span></div>
<div class="abs pop-link" style="left:767px;top:2193px"><svg class="frame" width="289" height="51" viewBox="0 0 289 51"><path d="M6 .5H268L288 25.5 268 50.5H6Q.5 50.5 .5 45V6Q.5 .5 6 .5Z" fill="#fff" stroke="#e6dcc6"/></svg><span class="text"><svg width="14" height="11" viewBox="0 0 14 11"><path d="M1 6l4 4 8-9" fill="none" stroke="#b39456" stroke-width="2"/></svg>Bangkok Flights</span></div>

<!-- footer -->
<div class="abs footer-brand">ROVANIX</div>
<nav class="abs footer-links"><span>HOME</span><span>ABOUT US</span><span>CUSTOMER SUPPORT</span><span>PRIVACY</span><span>TERMS OF USE</span></nav>
<p class="abs copyright">© 2016 ROVANIX. ALL RIGHTS RESERVED.</p>
<div class="abs skyline" role="img" aria-label="Golden city skyline silhouette along the bottom edge"></div>

</body>
</html>
```